New Webpage for High Class Expert Witness Services Company

We are looking for a minimalist design for a webpage that just has our logo and an entry form offer to connect with one of our Liaisons.
The entry form should just ask for Name, Email, Contact Info and Description of Project.

Company Name is: The Marlowe Crest Advisory Services

Number of Pages Required

1 page

```html
<!DOCTYPE html>
<html lang="en">
<head>
<meta charset="utf-8">
<title>The Marlowe Crest Advisory Services — Request a Consultation</title>
<link rel="stylesheet" href="https://fonts.googleapis.com/css2?family=Gilda+Display&family=Outfit:wght@400;500&display=swap">
<style>
  :root {
    --page-bg-top: #161616;
    --page-bg-bottom: #0d0d0d;
    --text-main: #ffffff;
    --text-soft: #f2f2f2;
    --brand-silver: #c9c9cb;
    --card-bg: #1c1c1c;
    --card-border: #2c2c2c;
    --field-bg: #1a1a1a;
    --field-border: #2e2e2e;
    --field-text: #e9e9e9;
    --button-top: #eaeaec;
    --button-bottom: #a6a6aa;
    --button-text: #111111;
    --footer-bg: #ffffff;
    --footer-text: #1a1a1a;
  }
  * { box-sizing: border-box; margin: 0; padding: 0; }
  html, body { width: 1200px; height: 1187px; overflow: hidden; }
  body {
    font-family: "Outfit", sans-serif;
    color: var(--text-main);
    background: linear-gradient(160deg, var(--page-bg-top), var(--page-bg-bottom));
    position: relative;
  }
  .brand {
    position: absolute; top: 78px; left: 0; width: 1200px;
    display: flex; justify-content: center; align-items: center; gap: 16px;
  }
  .brand-mark { width: 30px; height: 30px; background: var(--brand-silver); }
  .brand-name {
    font-family: "Gilda Display", serif;
    font-size: 36px; letter-spacing: 2px; color: var(--brand-silver);
    font-weight: 400; text-transform: uppercase;
  }
  .hero-title {
    position: absolute; top: 205px; left: 0; width: 1200px;
    text-align: center; font-family: "Gilda Display", serif;
    font-weight: 400; font-size: 78px; line-height: 88px; letter-spacing: 1px;
  }
  .hero-lead {
    position: absolute; top: 406px; left: 0; width: 1200px;
    text-align: center; font-size: 25px; color: var(--text-soft);
  }
  .consult-card {
    position: absolute; top: 489px; left: 221px; width: 757px; height: 558px;
    background: var(--card-bg); border: 1px solid var(--card-border);
    border-radius: 14px; padding: 0 32px;
    box-shadow: 0 20px 40px rgba(0,0,0,.35);
  }
  .card-title {
    font-family: "Gilda Display", serif; font-weight: 400;
    font-size: 34px; text-align: center; margin-top: 29px; height: 48px;
  }
  .consult-form { margin-top: 28px; display: flex; flex-direction: column; gap: 25px; }
  .field {
    width: 692px; height: 50px; background: var(--field-bg);
    border: 1px solid var(--field-border); border-radius: 3px;
    padding: 0 16px; font-family: "Outfit", sans-serif; font-size: 13px; color: var(--field-text);
  }
  .field::placeholder { color: var(--field-text); opacity: 1; }
  .field-message { height: 117px; padding-top: 17px; resize: none; }
  .submit-btn {
    margin-top: 8px; width: 692px; height: 45px; border: 0; border-radius: 3px;
    background: linear-gradient(0deg, var(--button-bottom), var(--button-top));
    font-family: "Outfit", sans-serif; font-weight: 500; font-size: 15px; color: var(--button-text);
  }
  .assurance {
    position: absolute; top: 1072px; left: 0; width: 1200px;
    text-align: center; font-size: 25px; color: var(--text-soft);
  }
  .site-footer {
    position: absolute; top: 1137px; left: 0; width: 1200px; height: 50px;
    background: var(--footer-bg); color: var(--footer-text);
    font-size: 12px; display: flex; align-items: center; justify-content: center;
  }
</style>
</head>
<body>
  <header class="brand">
    <span class="brand-mark" aria-hidden="true"></span>
    <span class="brand-name">Marlowe Crest Advisory Services</span>
  </header>

  <h1 class="hero-title">Trusted Expert Witness &amp;<br>Defense Support</h1>
  <p class="hero-lead">Connect with our professional liaisons for confidential case assistance.</p>

  <section class="consult-card">
    <h2 class="card-title">Request a Consultation</h2>
    <form class="consult-form">
      <input class="field" type="text" placeholder="Full Name*">
      <input class="field" type="email" placeholder="Email Address*">
      <input class="field" type="tel" placeholder="Phone Number*">
      <textarea class="field field-message" placeholder="Your message......"></textarea>
      <button class="submit-btn" type="submit">Submit</button>
    </form>
  </section>

  <p class="assurance">Confidential • Fast Response • Verified Experts</p>

  <footer class="site-footer">Copyright © 2026 The Marlowe Crest Advisory Services. All Rights Reserved.</footer>
</body>
</html>
```